Business Card Design Project

This is the first time we use our new logo. We need a business card that we can use both on our institutional corporate relationships and also that works for our staff that deals with consumers directly.

VELUNDA is a new company dedicated to empower consumers and to provide them with the best choices for specialized health care using the latest telemedicine technology (medicine at a distance via videoconference).

We want to print this cards in high quality materials and process. We will like designs that allow us to use UV spot varnish and other techniques that will differentiate us.

We are including Two different versions of Color logos. In addition we are including white over black background logos. Those can be used replacing the black for a color.

Please note this is the first time we will be creating any corporate materials with our new logo and colors.

Target Market(s)

34+ consumers of medium high and high socioeconomic levels.

Industry/Entity Type

Health

Requirements
Must have
• Our logo on its original colors
Should not have
• Any other graphical element or design that is not our logo

```html
<!DOCTYPE html>
<html lang="en">
<head>
<meta charset="utf-8">
<title>VELUNDA Business Card</title>
<link href="https://fonts.googleapis.com/css2?family=Montserrat:wght@500;700&family=Arimo:wght@400&display=swap" rel="stylesheet">
<style>
  :root {
    --backdrop: #e9e6e2;
    --card-white: #ffffff;
    --sky: #5ab4dc;
    --navy: #1c5a85;
    --navy-deep: #1b5480;
    --ink: #111418;
    --title-blue: #5ab4dc;
  }
  * { box-sizing: border-box; margin: 0; padding: 0; }
  html, body {
    width: 1200px; height: 872px; overflow: hidden;
    background: var(--backdrop);
  }
  .canvas {
    position: relative; width: 1200px; height: 872px;
  }
  .card {
    position: absolute; top: 68px; width: 420px; height: 735px;
    border-radius: 4px; overflow: hidden;
    box-shadow: 0 10px 28px rgba(0,0,0,0.18);
  }
  .card--front { left: 150px; background: var(--card-white); }
  .card--back { left: 630px; background: var(--navy-deep); }

  /* front */
  .front__top {
    height: 400px; position: relative;
    border-bottom: 3px solid var(--navy);
  }
  .wordmark {
    position: absolute; left: 0; right: 0; top: 200px;
    display: flex; align-items: center; justify-content: center; gap: 14px;
    font-family: "Montserrat", sans-serif; font-weight: 700;
    font-size: 52px; letter-spacing: 3px; color: var(--navy);
  }
  .wordmark__dot {
    width: 22px; height: 22px; border-radius: 50%; background: var(--sky);
  }
  .holder {
    position: absolute; left: 0; right: 0; bottom: 22px; text-align: center;
    font-family: "Montserrat", sans-serif; font-size: 28px;
  }
  .holder__name { font-weight: 700; color: var(--navy); }
  .holder__title { font-weight: 500; color: var(--title-blue); }

  .front__bottom {
    height: 335px; background: var(--sky);
    padding-top: 34px; display: flex; flex-direction: column; align-items: center;
    font-family: "Arimo", sans-serif; color: var(--ink);
  }
  .contact-list { list-style: none; }
  .contact-list li {
    display: flex; align-items: center; gap: 12px;
    font-size: 25px; line-height: 40px;
  }
  .contact-icon { width: 20px; height: 20px; flex: none; }
  .address {
    margin-top: 26px; text-align: center; font-size: 25px; line-height: 30px;
  }

  /* back */
  .back__mark {
    position: absolute; left: 0; right: 0; top: 300px;
    display: flex; align-items: center; justify-content: center; gap: 14px;
    font-family: "Montserrat", sans-serif; font-weight: 700;
    font-size: 50px; letter-spacing: 3px; color: var(--card-white);
  }
  .back__mark-dot {
    width: 22px; height: 22px; border-radius: 50%; background: var(--card-white);
  }
  .back__url {
    position: absolute; left: 0; right: 0; bottom: 90px; text-align: center;
    font-family: "Montserrat", sans-serif; font-weight: 500;
    font-size: 24px; letter-spacing: 6px; color: var(--card-white);
  }
</style>
</head>
<body>
<main class="canvas">
  <section class="card card--front" aria-label="Card front">
    <div class="front__top">
      <div class="wordmark"><span class="wordmark__dot"></span>VELUNDA</div>
      <p class="holder"><span class="holder__name">Your Name,</span> <span class="holder__title">Title</span></p>
    </div>
    <div class="front__bottom">
      <ul class="contact-list">
        <li>
          <svg class="contact-icon" viewBox="0 0 20 20" aria-hidden="true"><circle cx="10" cy="10" r="9" fill="none" stroke="#111418" stroke-width="2"/><path d="M7 5.5l2 2-1 1.5c.6 1.4 1.6 2.4 3 3l1.5-1 2 2-1.5 1.5C9.5 14 6 10.5 5.5 7z" fill="#111418"/></svg>
          012-345-6789
        </li>
        <li>
          <svg class="contact-icon" viewBox="0 0 20 20" aria-hidden="true"><circle cx="10" cy="10" r="9" fill="none" stroke="#111418" stroke-width="2"/><path d="M7 5.5l2 2-1 1.5c.6 1.4 1.6 2.4 3 3l1.5-1 2 2-1.5 1.5C9.5 14 6 10.5 5.5 7z" fill="#111418"/></svg>
          012-345-6789
        </li>
        <li>
          <svg class="contact-icon" viewBox="0 0 20 20" aria-hidden="true"><rect x="1.5" y="4.5" width="17" height="12" fill="none" stroke="#111418" stroke-width="2"/><path d="M2 5l8 6 8-6" fill="none" stroke="#111418" stroke-width="2"/></svg>
          name@velunda.com
        </li>
        <li>
          <svg class="contact-icon" viewBox="0 0 20 20" aria-hidden="true"><circle cx="10" cy="10" r="8.5" fill="none" stroke="#111418" stroke-width="2"/><ellipse cx="10" cy="10" rx="3.5" ry="8.5" fill="none" stroke="#111418" stroke-width="1.5"/><path d="M1.5 10h17M3 6h14M3 14h14" stroke="#111418" stroke-width="1.5"/></svg>
          www.velunda.com
        </li>
      </ul>
      <p class="address">Street Name, City Name<br>State, City Zip Code</p>
    </div>
  </section>

  <section class="card card--back" aria-label="Card back">
    <div class="back__mark"><span class="back__mark-dot"></span>VELUNDA</div>
    <p class="back__url">velunda.com</p>
  </section>
</main>
</body>
</html>
```